2 sided flyer for Insurance Servics

Would like a flyer that talks about who we are, our services, and our process. Attaching relevant information, as well as our Logo and other logos for a few larger insurance carriers that we have access to.

Target Market(s)

Financial Advisors and Insurance Agents

Industry/Entity Type

Finance and Insurance

Colors
0054AA
0677BA
7BADD7
CADEEF
E8F1F8
F0912C
F2A743
F7CA91
FBE8D2
FDF5EE

Requirements
Must have
• Lists, bullet points, pictures, and logos uploaded

```html
<!DOCTYPE html>
<html lang="en">
<head>
<meta charset="utf-8">
<title>Keystone Life Partners – Two-Sided Brokerage Flyer</title>
<link href="https://fonts.googleapis.com/css2?family=Montserrat:wght@500;600;700;800;900&family=Open+Sans:wght@400;600;700&display=swap" rel="stylesheet">
<style>
  :root{
    --navy:#23296e;
    --blue:#0054aa;
    --blue-mid:#0677ba;
    --blue-soft:#7badd7;
    --blue-pale:#cadeef;
    --blue-mist:#e8f1f8;
    --orange:#f0912c;
    --amber:#f2a743;
    --peach:#f7ca91;
    --cream:#fbe8d2;
    --ivory:#fdf5ee;
    --ink:#2a2d3e;
    --muted:#555a6c;
    --white:#ffffff;
    --stage:#eceef3;
  }
  *{margin:0;padding:0;box-sizing:border-box}
  html,body{width:800px;height:1200px;overflow:hidden;background:var(--stage)}
  body{font-family:"Open Sans",Arial,sans-serif;color:var(--ink)}
  .canvas{position:relative;width:800px;height:1200px;overflow:hidden}
  .page{position:absolute;top:317px;width:390px;height:565px;background:var(--white);overflow:hidden;box-shadow:0 2px 8px rgba(35,41,110,.12)}
  .page-front{left:5px}
  .page-back{left:405px}

  .heading{display:flex;align-items:center;gap:5px;font-family:"Montserrat",sans-serif;font-weight:800;color:var(--navy);line-height:1.1}
  .heading::before{content:"";flex:none;width:3px;height:1em;background:var(--amber)}
  .copy{font-size:6.3px;line-height:1.5;color:var(--muted)}

  /* front */
  .front-top{position:absolute;left:0;top:0;width:390px;height:262px;background:var(--navy)}
  .brand{position:absolute;left:14px;top:14px;display:flex;align-items:center;gap:6px;background:var(--white);padding:6px 8px}
  .brand-square{width:16px;height:16px;background:var(--blue)}
  .brand-name{font-family:"Montserrat",sans-serif;font-weight:800;font-size:7.5px;line-height:1.15;color:var(--navy);text-transform:uppercase;width:66px}
  .hero-photo{position:absolute;left:150px;top:14px;width:226px;height:128px;border-radius:6px;
    background:linear-gradient(135deg,#dfe3ea 0%,#bcc4d3 50%,#8e95aa 100%)}
  .headline{position:absolute;left:14px;top:152px;font-family:"Montserrat",sans-serif;font-weight:900;text-transform:uppercase;line-height:1}
  .headline span{display:block;color:var(--white);font-size:19px}
  .headline .key{color:var(--amber);font-size:34px;margin:3px 0 2px}
  .front-body{position:absolute;left:0;top:262px;width:390px;height:243px;display:flex}
  .about{width:200px;padding:12px 10px 0 14px}
  .about .heading{font-size:11px;margin-bottom:5px}
  .about .copy{margin-bottom:9px}
  .carriers{display:grid;grid-template-columns:1fr 1fr;gap:4px}
  .carrier{display:flex;align-items:center;gap:4px;height:17px;padding:0 5px;border:1px solid var(--blue-pale)}
  .carrier-mark{flex:none;width:6px;height:6px;background:var(--blue-mid)}
  .carrier-name{font-family:"Montserrat",sans-serif;font-weight:700;font-size:6px;color:var(--blue);white-space:nowrap}
  .why{width:176px;margin:10px 14px 0 0;padding:9px 9px 0;background:var(--ivory);border-top:3px solid var(--amber)}
  .why .heading{font-size:11px;margin-bottom:4px}
  .why-intro{font-size:6.3px;line-height:1.45;color:var(--muted);margin-bottom:6px}
  .why-list{list-style:none}
  .why-item{display:flex;gap:6px;margin-bottom:6px}
  .why-icon{flex:none;width:16px;height:16px;border-radius:50%;background:var(--amber);display:flex;align-items:center;justify-content:center}
  .why-name{font-family:"Montserrat",sans-serif;font-weight:800;font-size:6.4px;color:var(--navy);text-transform:uppercase;margin-bottom:1px}
  .why-text{font-size:5.8px;line-height:1.4;color:var(--muted)}

  .contact{position:absolute;left:0;bottom:0;width:390px;height:60px;background:var(--navy);padding:9px 14px 0;border-top:3px solid var(--amber)}
  .contact-title{font-family:"Montserrat",sans-serif;font-weight:900;font-size:13px;color:var(--amber);text-transform:uppercase;margin-bottom:4px}
  .contact-list{list-style:none}
  .contact-item{display:flex;align-items:center;gap:5px;color:var(--white);font-size:7px;font-weight:600;margin-bottom:3px}
  .contact-icon{width:10px;height:10px;border-radius:50%;background:var(--amber);display:flex;align-items:center;justify-content:center}
  .contact.inline{display:flex;align-items:center;gap:16px;padding-top:0}
  .contact.inline .contact-title{margin:0}
  .contact.inline .contact-list{display:flex;gap:14px}
  .contact.inline .contact-item{margin:0}

  /* back */
  .value{position:absolute;left:0;top:0;width:390px;height:250px;padding:14px 14px 0}
  .value > .heading{font-size:13px;margin-bottom:8px}
  .value-cols{display:flex;gap:12px}
  .value-col{width:175px}
  .sub{font-family:"Montserrat",sans-serif;font-weight:800;font-size:7.5px;color:var(--navy);margin:0 0 3px}
  .value-col .copy{margin-bottom:6px}
  .note{background:var(--cream);border-left:3px solid var(--amber);padding:5px 6px;margin-bottom:7px}
  .bullets{list-style:none}
  .bullets li{position:relative;padding-left:7px;font-size:6px;line-height:1.45;color:var(--muted);margin-bottom:2px}
  .bullets li::before{content:"";position:absolute;left:0;top:3px;width:3px;height:3px;background:var(--orange)}
  .note-blue{background:var(--blue-mist);border-left-color:var(--blue-mid)}

  .process{position:absolute;left:0;top:250px;width:390px;height:255px;display:flex}
  .process-panel{width:206px;background:var(--navy);padding:12px 12px 0 14px}
  .process-title{display:inline-block;font-family:"Montserrat",sans-serif;font-weight:900;font-size:11px;color:var(--navy);background:var(--amber);border-radius:10px;padding:4px 14px;margin-bottom:9px}
  .steps{list-style:none}
  .step{margin-bottom:7px}
  .step-name{display:flex;align-items:center;gap:5px;font-family:"Montserrat",sans-serif;font-weight:800;font-size:6.8px;color:var(--navy);background:var(--peach);border-radius:2px;padding:3px 5px;margin-bottom:3px}
  .step-num{width:11px;height:11px;border-radius:50%;background:var(--navy);color:var(--amber);font-size:6px;display:flex;align-items:center;justify-content:center}
  .step-text{font-size:5.9px;line-height:1.45;color:var(--white);padding-left:2px}
  .process-side{width:184px;padding:14px 14px 0 10px}
  .side-box{background:var(--blue-mist);border-left:3px solid var(--blue-mid);padding:6px 6px;margin-bottom:7px}
  .side-box .sub{font-size:6.8px}
</style>
</head>
<body>
<div class="canvas">

  <article class="page page-front">
    <header class="front-top">
      <div class="brand"><span class="brand-square"></span><span class="brand-name">Keystone Life Partners</span></div>
      <div class="hero-photo" role="img" aria-label="Photo of two advisors reviewing documents together at a laptop"></div>
      <h1 class="headline">
        <span>Full-Service</span>
        <span>Life Insurance</span>
        <span class="key">Brokerage</span>
        <span>General Agency</span>
      </h1>
    </header>

    <section class="front-body">
      <div class="about">
        <h2 class="heading">About Us</h2>
        <p class="copy">Keystone Life Partners is a full-service brokerage general agency built for financial advisors and insurance agents. We pair broad carrier access with expert case design and hands-on support, so you can place the right coverage with confidence.</p>
        <h2 class="heading">List of Carriers Include</h2>
        <div class="carriers">
          <div class="carrier"><span class="carrier-mark"></span><span class="carrier-name">Harborline Life</span></div>
          <div class="carrier"><span class="carrier-mark"></span><span class="carrier-name">Crestway Mutual</span></div>
          <div class="carrier"><span class="carrier-mark"></span><span class="carrier-name">Northfield Assurance</span></div>
          <div class="carrier"><span class="carrier-mark"></span><span class="carrier-name">Meridian Trust Life</span></div>
          <div class="carrier"><span class="carrier-mark"></span><span class="carrier-name">Oakridge Life</span></div>
          <div class="carrier"><span class="carrier-mark"></span><span class="carrier-name">Bayshore Life</span></div>
          <div class="carrier"><span class="carrier-mark"></span><span class="carrier-name">Summit Financial Life</span></div>
          <div class="carrier"><span class="carrier-mark"></span><span class="carrier-name">Atlas General Life</span></div>
          <div class="carrier"><span class="carrier-mark"></span><span class="carrier-name">Evergreen Protective</span></div>
          <div class="carrier"><span class="carrier-mark"></span><span class="carrier-name">Pinegate Life</span></div>
        </div>
      </div>

      <div class="why">
        <h2 class="heading">Why KLP?</h2>
        <p class="why-intro">When you choose to work with us, you will see the value from your very first case.</p>
        <ul class="why-list">
          <li class="why-item"><span class="why-icon"><svg width="9" height="9" viewBox="0 0 20 20"><path d="M4 10l4 4 8-8" fill="none" stroke="#fff" stroke-width="3" stroke-linecap="round"/></svg></span><div><h3 class="why-name">Underwriting</h3><p class="why-text">Experienced underwriters review each case early for the best offer.</p></div></li>
          <li class="why-item"><span class="why-icon"><svg width="9" height="9" viewBox="0 0 20 20"><rect x="3" y="3" width="14" height="14" fill="none" stroke="#fff" stroke-width="2.5"/></svg></span><div><h3 class="why-name">Advanced Case Design</h3><p class="why-text">Tailored illustrations for estate, business and income needs.</p></div></li>
          <li class="why-item"><span class="why-icon"><svg width="9" height="9" viewBox="0 0 20 20"><circle cx="10" cy="10" r="7" fill="none" stroke="#fff" stroke-width="2.5"/></svg></span><div><h3 class="why-name">Case Management</h3><p class="why-text">A dedicated manager tracks every requirement until placement.</p></div></li>
          <li class="why-item"><span class="why-icon"><svg width="9" height="9" viewBox="0 0 20 20"><path d="M3 14l5-5 3 3 6-6" fill="none" stroke="#fff" stroke-width="3" stroke-linecap="round"/></svg></span><div><h3 class="why-name">Competitive Compensation</h3><p class="why-text">Strong contracts and timely payouts for the work you bring.</p></div></li>
          <li class="why-item"><span class="why-icon"><svg width="9" height="9" viewBox="0 0 20 20"><path d="M11 2L4 11h5l-1 7 7-9h-5z" fill="#fff"/></svg></span><div><h3 class="why-name">Fast Turnaround</h3><p class="why-text">Quick quotes and lean paperwork get clients covered sooner.</p></div></li>
        </ul>
      </div>
    </section>

    <footer class="contact">
      <h2 class="contact-title">Contact Us</h2>
      <ul class="contact-list">
        <li class="contact-item"><span class="contact-icon"><svg width="6" height="6" viewBox="0 0 14 14"><rect x="1" y="3" width="12" height="8" fill="none" stroke="#fff" stroke-width="2"/></svg></span>hello@keystonelifepartners.com</li>
        <li class="contact-item"><span class="contact-icon"><svg width="6" height="6" viewBox="0 0 14 14"><circle cx="7" cy="7" r="5.5" fill="none" stroke="#fff" stroke-width="2"/></svg></span>www.keystonelifepartners.com</li>
      </ul>
    </footer>
  </article>

  <article class="page page-back">
    <section class="value">
      <h2 class="heading">Our Value</h2>
      <div class="value-cols">
        <div class="value-col">
          <p class="copy">We give independent advisors the tools, carriers and people they need to grow a lasting life insurance practice.</p>
          <h3 class="sub">Our Point of View</h3>
          <p class="copy">Every client deserves coverage designed around real goals, and every advisor deserves a partner who answers quickly.</p>
          <div class="note">
            <ul class="bullets">
              <li>Access to top-rated life carriers</li>
              <li>Side-by-side product comparisons</li>
              <li>Informal inquiries at no cost</li>
              <li>Marketing and sales support</li>
            </ul>
          </div>
          <h3 class="sub">Our Commitment</h3>
          <p class="copy">Clear communication, honest guidance and steady follow-through on every case.</p>
        </div>
        <div class="value-col">
          <h3 class="sub">Our Concierge Services Team</h3>
          <p class="copy">Our concierge team handles the details so you can stay focused on your clients and your next meeting.</p>
          <div class="note note-blue">
            <ul class="bullets">
              <li>Paramedical exam scheduling</li>
              <li>Medical records ordering</li>
              <li>Application review for accuracy</li>
              <li>Status updates on every case</li>
              <li>Policy delivery coordination</li>
            </ul>
          </div>
          <p class="copy">One call connects you with a team that knows your business and your clients by name.</p>
        </div>
      </div>
    </section>

    <section class="process">
      <div class="process-panel">
        <h2 class="process-title">Our Process</h2>
        <ol class="steps">
          <li class="step"><h3 class="step-name"><span class="step-num">1</span>Case Review &amp; Quote</h3><p class="step-text">Share your client's needs and we return quotes from several carriers.</p></li>
          <li class="step"><h3 class="step-name"><span class="step-num">2</span>Application Submitted</h3><p class="step-text">We check every form and submit a clean application to the carrier.</p></li>
          <li class="step"><h3 class="step-name"><span class="step-num">3</span>Underwriting &amp; Approval</h3><p class="step-text">Our team works with underwriters to secure the best possible offer.</p></li>
          <li class="step"><h3 class="step-name"><span class="step-num">4</span>Policy Delivery &amp; Support</h3><p class="step-text">We deliver the policy and stay with you for future service needs.</p></li>
        </ol>
      </div>
      <div class="process-side">
        <div class="side-box"><h3 class="sub">Dedicated Case Manager</h3><p class="copy">One contact follows your case from quote to placement.</p></div>
        <div class="side-box"><h3 class="sub">Underwriting Insight</h3><p class="copy">Early field underwriting helps avoid surprises later.</p></div>
        <div class="side-box"><h3 class="sub">Ongoing Support</h3><p class="copy">Reviews, conversions and in-force service after the sale.</p></div>
      </div>
    </section>

    <footer class="contact inline">
      <h2 class="contact-title">Contact Us</h2>
      <ul class="contact-list">
        <li class="contact-item"><span class="contact-icon"><svg width="6" height="6" viewBox="0 0 14 14"><rect x="1" y="3" width="12" height="8" fill="none" stroke="#fff" stroke-width="2"/></svg></span>hello@keystonelifepartners.com</li>
        <li class="contact-item"><span class="contact-icon"><svg width="6" height="6" viewBox="0 0 14 14"><circle cx="7" cy="7" r="5.5" fill="none" stroke="#fff" stroke-width="2"/></svg></span>www.keystonelifepartners.com</li>
      </ul>
    </footer>
  </article>

</div>
</body>
</html>
```